CANNABIS BASED BUSINESS CARD DESIGN AND CREATION

WE ARE A PRIVATELY OWNED INVESTMENT CORPORATION. WE PRIMARILY INVEST IN LEGAL PUBLICALLY TRADED CANNABIS COMPANIES THAT ARE TRADED THROUGH THE OTC OR VOLTRIX. WE OFFER THE PUBLIC AN OPPORTUNITY TO PARTICIPATE DIRECTLY WITH THESE COMPANIES FOR NO FEES, NO COMMISSIONS AND IN DEPTH RESEARCH ON EVERY COMPANY PROFILE. WE ARE ALSO PRO FEDERAL LEGALIZATION AND WILL APPLY FOR CULTIVATION AND DISPENSARY LICENSES WHEN THEY BECOME AVAILABLE.

Target Market(s)

30-60 FEMALE AND MALE INVESTORS

Industry/Entity Type

Business

Contact Information for Business Card

TQM CAPITAL GROUP MARLA J PENDLEBURY(469) 426-6302ERIN@EDSCAPITALGROUP.COM

Font styles to use
Decorative

Requirements
Must have
• COMPANY LOGO
• CANNABIS LOGO
Nice to have
• MODERN FONT AND LOGOS

```html
<!DOCTYPE html>
<html lang="en">
<head>
<meta charset="utf-8">
<title>TQM Capital Group – Business Card</title>
<link href="https://fonts.googleapis.com/css2?family=Lato:wght@400;700&display=swap" rel="stylesheet">
<style>
  :root {
    --page-bg: #2b2b2b;
    --card-bg: #050505;
    --card-edge: #141414;
    --accent: #f39220;
    --text-light: #f2f2f2;
    --text-soft: #e6e6e6;
    --mark-faint: #161616;
    --divider: #262626;
  }
  * { box-sizing: border-box; margin: 0; padding: 0; }
  html, body {
    width: 1200px; height: 900px; overflow: hidden;
    background: var(--page-bg);
    font-family: "Lato", sans-serif;
  }
  .canvas {
    position: relative; width: 1200px; height: 900px;
  }
  .card {
    position: absolute; left: 270px;
    width: 660px; height: 376px;
    border-radius: 18px;
    background: radial-gradient(ellipse at 30% 30%, #111 0%, var(--card-bg) 70%);
    box-shadow: 0 10px 30px rgba(0,0,0,.45);
    overflow: hidden;
  }
  .card--back { top: 56px; }
  .card--front { top: 468px; }

  /* back side */
  .back-watermark {
    position: absolute; left: 110px; top: 90px;
    width: 230px; height: 230px; border-radius: 50%;
    border: 6px solid var(--mark-faint);
  }
  .back-brand {
    position: absolute; left: 330px; top: 150px;
    display: flex; align-items: center; gap: 14px;
  }

  .brand-dot {
    width: 40px; height: 40px; border-radius: 50%;
    border: 3px solid var(--text-light);
    flex: none;
  }
  .brand-name {
    font-weight: 400; font-size: 21px; letter-spacing: 1.5px;
    color: var(--text-light); white-space: nowrap;
  }

  /* front side */
  .front-brand {
    position: absolute; right: 338px; top: 112px;
    display: flex; flex-direction: column; align-items: flex-end; gap: 16px;
  }
  .divider {
    position: absolute; left: 340px; top: 92px;
    width: 1px; height: 200px; background: var(--divider);
  }
  .contact {
    position: absolute; left: 366px; top: 120px;
  }
  .contact__name {
    font-weight: 400; font-size: 18px; letter-spacing: .4px;
    color: var(--accent); text-transform: uppercase;
    margin-bottom: 34px;
  }
  .contact__list { list-style: none; }
  .contact__item {
    display: flex; align-items: center; gap: 10px;
    font-size: 13.5px; color: var(--text-soft);
    height: 23px;
  }
  .contact__icon { width: 13px; height: 13px; flex: none; }
  .contact__icon path, .contact__icon rect { fill: var(--accent); }
  .contact__icon .stroke { fill: none; stroke: var(--accent); stroke-width: 2; stroke-linecap: round; }
</style>
</head>
<body>
<main class="canvas">

  <section class="card card--back" aria-label="Card back">
    <div class="back-watermark"></div>
    <div class="back-brand">
      <span class="brand-dot"></span>
      <span class="brand-name">TQM CAPITAL GROUP</span>
    </div>
  </section>

  <section class="card card--front" aria-label="Card front">
    <div class="front-brand">
      <span class="brand-dot"></span>
      <span class="brand-name">TQM CAPITAL GROUP</span>
    </div>

    <div class="divider"></div>

    <div class="contact">
      <p class="contact__name">Marla J Pendlebury</p>
      <ul class="contact__list">
        <li class="contact__item">
          <svg class="contact__icon" viewBox="0 0 16 16" aria-hidden="true">
            <path d="M2 6c0-2 2-3 6-3s6 1 6 3v1h-3V5.5H5V7H2z"/>
            <rect x="3" y="8" width="10" height="6" rx="1.5"/>
          </svg>
          (555) 013-4478
        </li>
        <li class="contact__item">
          <svg class="contact__icon" viewBox="0 0 16 16" aria-hidden="true">
            <path d="M1 3h14v10H1z M2.5 4.5 8 9l5.5-4.5" />
          </svg>
          marla@tqmcapitalgroup-demo.com
        </li>
        <li class="contact__item">
          <svg class="contact__icon" viewBox="0 0 16 16" aria-hidden="true">
            <path class="stroke" d="M7 9.5 9.5 7 M6 7.5 4 9.5a2.1 2.1 0 0 0 3 3l2-2 M10 8.5l2-2a2.1 2.1 0 0 0-3-3l-2 2"/>
          </svg>
          www.tqmcapitalgroup-demo.com
        </li>
      </ul>
    </div>
  </section>

</main>
</body>
</html>
```